Luxury sell sheet flyer Design

We need two luxury/premium looking sales flyer - one for luxury and one for travel-

Please find flyers from last year (2015) attached. Please copy the pictures and the look and feel (and colors), and use the content form the 2016 documents.

These flyers will be used for corporate subscription sales and targetted at CMOs and Marketing heads. As such they should convey a very premium look and feel.

Please provide in format that we can make text edits in later.

USA, UK, Asia

Travel

Serif

• Good copyright free pictures, no clip art, that show a very premium look and feel for a corporate flyer
• clean feel, not cluttered
• clip art

```html
<!DOCTYPE html>
<html lang="en">
<head>
<meta charset="utf-8">
<title>2016 Affluent Compass Travel Subscription Service</title>
<link rel="stylesheet" href="https://fonts.googleapis.com/css2?family=Montserrat:wght@500&family=Tinos&family=Arimo:ital,wght@0,400;0,700;1,400&display=swap">
<style>
  :root {
    --navy: #0d3b5c;
    --sky-light: #eef6fc;
    --sky-mid: #bcdcf2;
    --tan: #d8c3a8;
    --box-top: #46a8d6;
    --box-bottom: #1c74b1;
    --drop-blue: #2a86c2;
    --ink: #1c1c1c;
    --plus-dark: #a6a6a6;
    --plus-light: #e8e8e8;
    --premium-dark: #d48f58;
    --premium-light: #f3dcc6;
    --prestige-dark: #b48d1c;
    --prestige-light: #eedfa8;
  }
  * { margin: 0; padding: 0; box-sizing: border-box; }
  html, body { width: 927px; height: 1200px; overflow: hidden; }
  body { position: relative; background: linear-gradient(180deg, #ffffff 50%, #e7f2fb 100%); font-family: "Tinos", serif; }

  .hero-photo {
    position: absolute; left: 0; top: 0; width: 927px; height: 590px;
    background: linear-gradient(100deg, #d9ecf9 0%, #f4f9fd 35%, #b9d3e6 62%, #6f8697 78%, #d5e7f4 100%);
  }
  .hero-band { position: absolute; left: 0; top: 590px; width: 927px; height: 18px; background: var(--tan); }

  .title {
    position: absolute; left: 74px; top: 82px;
    font-family: "Montserrat", sans-serif; font-weight: 500;
    font-size: 53px; line-height: 59px; color: var(--navy); letter-spacing: 0.3px;
  }

  .intro {
    position: absolute; left: 49px; top: 654px; width: 472px;
    font-size: 16.4px; line-height: 23.6px; color: var(--ink);
  }
  .drop-cap {
    float: left; width: 38px; height: 38px; margin: 2px 2px 0 0;
    background: var(--drop-blue); color: #fff;
    font-size: 40px; line-height: 40px; text-align: center;
  }

  .offerings {
    position: absolute; left: 534px; top: 643px; width: 356px; height: 322px;
    border-radius: 13px; color: #fff;
    background: linear-gradient(160deg, var(--box-top), var(--box-bottom));
    font-family: "Arimo", sans-serif; padding: 30px 20px 0 24px;
  }
  .offerings h2 { font-size: 16.5px; line-height: 21px; font-weight: 700; margin-bottom: 14px; }
  .offerings ol { list-style: none; counter-reset: item; }
  .offerings li { counter-increment: item; position: relative; padding-left: 38px; font-size: 16px; line-height: 20px; margin-bottom: 13px; }
  .offerings li::before { content: counter(item) "."; position: absolute; left: 14px; }

  .price-table {
    position: absolute; left: 538px; top: 1009px; width: 350px;
    border-collapse: collapse; font-family: "Arimo", sans-serif;
  }
  .price-table th, .price-table td { height: 29px; padding: 0 6px; border-bottom: 2px solid #fff; }
  .price-table th { background: #000; color: #fff; font-weight: 400; text-align: left; }
  .price-table th.level { font-size: 13px; font-style: italic; width: 227px; }
  .price-table th.tier { font-size: 16px; text-align: center; }
  .price-table td.level { color: #fff; font-size: 16px; }
  .price-table td.price { font-style: italic; font-size: 16px; color: #222; text-align: center; }
  .price-table b { font-weight: 700; }
  .tier-plus .level { background: var(--plus-dark); }
  .tier-plus .price { background: var(--plus-light); }
  .tier-premium .level { background: var(--premium-dark); }
  .tier-premium .price { background: var(--premium-light); }
  .tier-prestige .level { background: var(--prestige-dark); }
  .tier-prestige .price { background: var(--prestige-light); }

  .footer-rule { position: absolute; left: 49px; top: 1160px; width: 482px; height: 6px; border-top: 1px solid #8a97a3; border-bottom: 1px solid #8a97a3; }
  .footer-title {
    position: absolute; left: 538px; top: 1155px;
    font-family: "Arimo", sans-serif; font-weight: 700; font-size: 13.2px;
    color: var(--navy); letter-spacing: 0.2px;
  }
</style>
</head>
<body>
  <div class="hero-photo" role="img" aria-label="Smiling businessman in a grey suit seated in an airport lounge with a tablet and rolling suitcase"></div>
  <div class="hero-band"></div>

  <h1 class="title">2016<br>Affluent Compass<br>Travel Subscription<br>Service</h1>

  <div class="intro">
    <span class="drop-cap">A</span>ffluent Asian consumers continue to be the leading travellers into 2016, with increasing numbers heading to global travel destinations. These travellers are driving premium travel service and luxury goods consumption across Asia and globally. Brands and marketers need to increasingly monitor the pulse of these discerning consumers to uncover their trends and purchase preferences. At Meridian Research we have exclusive access to engage with this hard to reach customer base through our VelvetCircle™ community. A closed door, invitation only community of affluent and HNWI consumers across 20 key markets built through key luxury partnerships.<br>
    To cater to a growing response of requests from travel brands and those marketing to traveling consumers, we at Meridian have designed an annual program – The Meridian Affluent Compass™ a subscription service that provides market and category specific data, updated every six months, aimed at uncovering the trends, consumption patterns, brand preferences, and detailed insights of the Affluent travel consumers in key Asian markets.
  </div>

  <section class="offerings">
    <h2>The subscription service comprises of four offerings:</h2>
    <ol>
      <li>Affluent Asian Travel Consumer Reports (semi-annual)</li>
      <li>Semi-annual Roundtables with Senior Executives from the Luxury Travel World</li>
      <li>Custom Tabulations of Data (semi-annual)</li>
      <li>Semi-annual Brainstorming Sessions with Meridian Experts</li>
    </ol>
  </section>

  <table class="price-table">
    <tr><th class="level">Subscription Level:</th><th class="tier">Price Tiers</th></tr>
    <tr class="tier-plus"><td class="level">Affluent Compass <b>PLUS</b></td><td class="price">USD 19,500</td></tr>
    <tr class="tier-premium"><td class="level">Affluent Compass <b>PREMIUM</b></td><td class="price">USD 22,500</td></tr>
    <tr class="tier-prestige"><td class="level">Affluent Compass <b>PRESTIGE</b></td><td class="price">USD 26,500</td></tr>
  </table>

  <div class="footer-rule"></div>
  <div class="footer-title">2016 Affluent Compass Travel Subscription Service</div>
</body>
</html>
```